New Corporate Email Signature with Custom GIF KAV Electric LLC & KAV Fire & Security

Project Overview
KAV Electric LLC and KAV Fire & Security are seeking a professional, polished, and technically robust corporate email signature design. The project has two integrated deliverables:
A custom animated GIF representing both sides of our business
A complete corporate email signature layout designed for real-world compatibility (Gmail, Outlook, iOS, Android)
Our brand aesthetic is corporate, conservative, and clean. We value clarity, trust, professionalism, and subtle creativity β€” nothing overly flashy or cartoonish.
This design will be used across the entire company and must be visually aligned with our brand while remaining technically dependable.

PART 1 β€” Animated GIF Requirements
The GIF will be the core visual anchor of the new signature.
It must be clean, smooth, subtle, and optimized for email use.
βš™ Technical Requirements
Max file size: 150–200 KB (smaller is better)
Dimensions: approx 300px width (flexible, but must look good small)
Looping: continuous loop
Style: professional, minimalistic transitions

No rapid flashing or harsh animations
Must export cleanly into a format email clients accept

🎞 GIF Animation Sequence
Phase 1 β€” KAV Electric (KE)
Use the yellow β€œKE” avatar logo (provided).
Animation flow:
KE avatar appears
Full name β€œKAV Electric LLC” slides in, fades in, or otherwise appears smoothly
A scrolling or cycling list of service offerings displays:
EV Charging Stations
Generator & Transformers
Testing & Troubleshooting
LED Lighting Upgrades
After the list is shown, the entire KE segment fades out

Phase 2 β€” KAV Fire & Security (KF)
Use the red β€œKF” avatar logo (provided).
Animation flow mirrors Phase 1:
KF avatar appears
Full name β€œKAV Fire & Security” slides/fades in
Scrolling or cycling list of services displays:
Fire Alarm Upgrades
BQTL 48 Test & Inspect
Security Surveillance Systems
Access Control Systems
Data & Fiber Optic Cabling
Fade out β†’ loop back to KE
Creative Direction

Designers are encouraged to use:
Clean transitions
Soft fades
Professional typography
Modern minimalism
Consistent brand colors
High clarity at small sizes

Avoid:
Busy motion
Hard flashes
Excessive text overlays
Overly long transitions

The goal: a smooth, corporate-grade rotation that fits seamlessly into an email signature.

PART 2 β€” Corporate Email Signature Design

The signature must be visually appealing, brand-aligned, and structurally bulletproof across all major email systems.
πŸ“ Required Elements
πŸ‘€ Left Side Content
Circular headshot (we will supply final photos)
Social media icons with embedded URLs:
Facebook
LinkedIn
Google Business Profile
Instagram

Icons should be clean, modern, and in alignment with brand colors
πŸ“„ Right Side Content
Name
Title
KAV Electric LLC / KAV Fire & Security (depending on user)
Phone number
Email address
License# 52804
Physical office address: 384 Pembrook St, Lakeford PA 19412

Small CTA for newsletter signup (button or micro-banner)

🏒 Branding Assets Provided

You will receive:
KE avatar logo
KF avatar logo
Full-name KE logo
Full-name KF logo

These should be incorporated naturally and professionally.

Design Requirements

Conservative corporate styling

Clean typography

Balanced use of white space

Professional hierarchy

Light and dark mode compatibility preferred

Layout should not rely on one large image

All images should export cleanly for hosting on servers/CDN

Avoid overly tall signatures

The final signature must present as modern, trustworthy, and technically reliable across platforms.

πŸ§ͺ Compatibility Requirements

The signature must display correctly in:

Gmail (web and mobile)

Outlook (desktop & online)

Apple Mail

iPhone Mail

Android mail apps

Designers must avoid DIV-based layouts and instead propose a layout that can be implemented using table-based HTML, which is the industry standard for email compatibility.

You do not need to build the HTML β€” only supply the final layered design (PSD/AI/Figma) plus a clear structural layout that can be converted to HTML later.

πŸ“¦ Deliverables
1. Animated GIF

Final optimized GIF

Source file (After Effects, Photoshop, or equivalent)

Export guidelines so we can reproduce future versions

2. Email Signature Design

Full static design mockup

Modular layout for each employee

Icon set for social media

Newsletter CTA element

Clear spacing, alignment, and typography specifications

All source files (PSD, AI, Figma, etc.)

🧭 Creative Guidance Summary

We want:
βœ” Modern
βœ” Corporate
βœ” Minimalistic
βœ” Professional
βœ” Clean motion
βœ” Consistent branding
βœ” Email-safe elements

We do not want:
✘ Flashy marketing look
✘ Overly colorful or playful styles
✘ Hard-to-read fonts
✘ Heavy animation
✘ Oversized signatures

πŸ›  Tools & Format Flexibility

We allow full creative freedom regarding:

Animation style

Typography choices

Structuring of the two-column layout

How the service lists scroll or cycle

As long as the end result is clean, brand-aligned, professional, and email-compatible.

πŸ’¬ Final Note to Designers

We encourage creativity within the boundaries of corporate professionalism.
This signature will represent our company every time an email is sent β€” it must communicate trust, clarity, expertise, and brand strength.

```html
<!DOCTYPE html>
<html lang="en">
<head>
<meta charset="utf-8">
<title>KAV Electric LLC – Email Signature</title>
<link rel="stylesheet" href="https://fonts.googleapis.com/css2?family=Montserrat:wght@600;700&family=Inter:wght@400;500&display=swap">
<style>
  :root {
    --stage-bg: #d4d5d7;
    --card-bg: #ffffff;
    --ink-grey: #767676;
    --ink-dark: #1e1e1e;
    --brand-yellow: #e6c800;
    --social-grey: #7a7a7a;
    --photo-top: #c9d3dc;
    --photo-bottom: #2b3a55;
  }
  * { box-sizing: border-box; margin: 0; padding: 0; }
  html, body {
    width: 1200px; height: 576px; overflow: hidden;
    background: var(--stage-bg);
  }
  .signature {
    position: absolute; left: 202px; top: 146px;
    width: 801px; height: 268px;
    background: var(--card-bg);
    box-shadow: 0 0 40px rgba(0,0,0,0.08);
  }
  .headshot {
    position: absolute; left: 51px; top: 18px;
    width: 160px; height: 160px; border-radius: 50%;
    border: 3px solid var(--brand-yellow);
    padding: 5px; background: var(--card-bg);
  }
  .headshot__photo {
    width: 100%; height: 100%; border-radius: 50%;
    background: linear-gradient(180deg, var(--photo-top) 0%, #8b9bb0 50%, var(--photo-bottom) 100%);
  }
  .socials {
    position: absolute; left: 14px; top: 199px;
    display: flex; gap: 10px; list-style: none;
  }
  .socials__item {
    width: 52px; height: 52px; border-radius: 50%;
    background: var(--social-grey);
  }
  .details {
    position: absolute; right: 16px; top: 0;
    text-align: right;
  }
  .details__name {
    position: absolute; right: 0; top: 16px; white-space: nowrap;
    font: 700 29px/1 "Montserrat", sans-serif; color: var(--ink-grey);
  }
  .details__title {
    position: absolute; right: 0; top: 55px; white-space: nowrap;
    font: 500 20px/1 "Inter", sans-serif; color: var(--ink-grey);
  }
  .company {
    position: absolute; right: 0; top: 90px; white-space: nowrap;
    display: flex; align-items: center; gap: 10px;
    font: 700 26px/1 "Montserrat", sans-serif; color: var(--ink-grey);
    letter-spacing: 0.5px;
  }
  .company__dot {
    width: 18px; height: 18px; border-radius: 50%;
    background: var(--brand-yellow);
  }
  .contact-line {
    position: absolute; right: 0; white-space: nowrap;
    display: flex; align-items: center; gap: 8px;
    font: 400 20px/1 "Inter", sans-serif; color: var(--ink-dark);
  }
  .contact-line--phone { top: 129px; }
  .contact-line--address { top: 160px; }
  .contact-line--license { top: 191px; }
  .contact-line__group { display: flex; align-items: center; gap: 8px; }
  .contact-line__group + .contact-line__group { margin-left: 18px; }
  .icon { width: 20px; height: 20px; fill: var(--brand-yellow); flex: none; }
  .newsletter-button {
    position: absolute; right: -6px; top: 223px;
    width: 221px; height: 36px; border-radius: 18px;
    background: var(--brand-yellow);
    font: 500 20px/36px "Inter", sans-serif; color: var(--ink-dark);
    text-align: center; text-decoration: none; white-space: nowrap;
  }
</style>
</head>
<body>
  <section class="signature">
    <div class="headshot">
      <div class="headshot__photo" role="img" aria-label="Circular headshot of the team member"></div>
    </div>
    <ul class="socials">
      <li class="socials__item" role="img" aria-label="Social profile link 1"></li>
      <li class="socials__item" role="img" aria-label="Social profile link 2"></li>
      <li class="socials__item" role="img" aria-label="Business listing link"></li>
      <li class="socials__item" role="img" aria-label="Social profile link 3"></li>
    </ul>

    <div class="details">
      <h1 class="details__name">Daniel Marcori</h1>
      <p class="details__title">CEO</p>
      <p class="company"><span class="company__dot"></span>KAV Electric LLC</p>

      <p class="contact-line contact-line--phone">
        <span class="contact-line__group">
          <svg class="icon" viewBox="0 0 24 24" aria-hidden="true"><path d="M6.6 10.8a15.2 15.2 0 0 0 6.6 6.6l2.2-2.2a1 1 0 0 1 1-.25 11.4 11.4 0 0 0 3.6.57 1 1 0 0 1 1 1V20a1 1 0 0 1-1 1A17 17 0 0 1 3 4a1 1 0 0 1 1-1h3.5a1 1 0 0 1 1 1c0 1.25.2 2.45.57 3.57a1 1 0 0 1-.25 1z"/></svg>
          +1 555 014 2290
        </span>
        <span class="contact-line__group">
          <svg class="icon" viewBox="0 0 24 24" aria-hidden="true"><path d="M2 5h20v14H2z"/><path d="M2.5 5.5l9.5 6.8 9.5-6.8" fill="none" stroke="#fff" stroke-width="1.6"/></svg>
          info@kavelectric.com
        </span>
      </p>
      <p class="contact-line contact-line--address">
        <svg class="icon" viewBox="0 0 24 24" aria-hidden="true"><path d="M12 2a7 7 0 0 0-7 7c0 5.2 7 13 7 13s7-7.8 7-13a7 7 0 0 0-7-7zm0 9.5A2.5 2.5 0 1 1 12 6.5a2.5 2.5 0 0 1 0 5z"/></svg>
        384 Pembrook St, Lakeford PA 19412
      </p>
      <p class="contact-line contact-line--license">License# 52804</p>

      <a class="newsletter-button" href="#">Join the Newsletter</a>
    </div>
  </section>
</body>
</html>
```